Web Site Design For Real Estate Sales Project

The idea behind this project is pretty simple. I am putting my penthouse apartment up for sale and am trying to be creative in selling it.
Technically this will be pretty simple, it will be 3 pages but graphically this has to be as impressive as possible which is why I am trying Pixel Harbor.
The apartment is located in Barra Da Tijuca, Rio De Janeiro, Brazil. (This is where the 2016 Solstice Meet will be held)
I am looking for an index page and 2 sub-pages. I am open to all kinds of designs and navigation's but it has to make an impression quickly with a professional and enticing design. The index page should make it obvious that there is a penthouse apartment for sale in Barra Da Tijuca ( suburb of Rio De Janeiro). The first sub page is about the Condominium where the apartment is located, the second sub page is about the apartment itself.
Here is a more detailed description of what the 3 pages should be about.
Index Page
This is the landing page and should make it obvious that there is an apartment for sale in Barra Da Tijuca, Rio De Janeiro with the following attributes
251 SQ M
Duplex Penthouse
4 suites
Price R$ 2.200.000
Price per SQ M: R$ 8.764
First Sub-Page
This is about the Condominium which is called "Tranquil Cliff Suites" with the following bullets
*Family friendly and safe
*Direct access to the beach
*Many amenities like pool, football court, gym, sauna
There should be some photos of the condominium and a link to the site of the condominium ( www.tcsqv.com )
Second Sub-page
This is about the apartment. It should list in bullets the features of the apartment and then have a photo gallery of the view and various rooms. I have attached sample photos but will eventually have to use more photos.
Apartment Features
Price: R$ 2.220.000
251 m2 Duplex Penthouse
4 suites
maids room with bath
guest bathroom
living room
dinning room
Terrace with heated pool for year round use
Veranda
As mentioned above I am open to all designs and navigation so feel free to be creative. The important thing is catch peoples attention and get the message across in a few seconds, which is that there is an apartment for sale at this price with these features in this location. I will then use zintra clickreach and SEO to get people to the site.
Thanks
Men and Women from 30-60 years of age.
Apartment

```html
<!DOCTYPE html>
<html lang="en">
<head>
<meta charset="utf-8">
<title>Skyline Residence – Penthouse for sale in Barra Da Tijuca</title>
<link rel="stylesheet" href="https://fonts.googleapis.com/css2?family=Source+Sans+3:wght@300;400&family=Dancing+Script:wght@400&display=swap">
<style>
  :root {
    --accent: #2bb3e0;
    --text: #5a5a5a;
    --text-dark: #444;
    --rule: #e6e6e6;
    --panel: #e9e9e9;
    --frame: #dcdcdc;
    --page: #fdfdfd;
    --header-band: rgba(22, 40, 58, 0.72);
    --caption-band: rgba(20, 24, 18, 0.55);
    --white: #ffffff;
  }
  * { margin: 0; padding: 0; box-sizing: border-box; }
  html, body { width: 1024px; height: 1200px; overflow: hidden; }
  body {
    position: relative;
    background: var(--page);
    font-family: "Source Sans 3", "Myriad Pro", Arial, sans-serif;
    font-weight: 300;
    color: var(--text);
  }
  a { color: inherit; text-decoration: none; }

  /* Hero */
  .hero {
    position: absolute; left: 0; top: 0; width: 1024px; height: 480px;
    background:
      linear-gradient(180deg, #3f5f73 0%, #56707a 12%, transparent 30%),
      linear-gradient(160deg, #1d4f78 0%, #1f5a86 28%, #8f9a92 45%, #6c7a5e 60%, #4c6338 78%, #2f4021 100%);
  }
  .hero-lake {
    position: absolute; right: 40px; top: 95px; width: 190px; height: 95px;
    background: radial-gradient(ellipse at center, #b8c6cc 0%, rgba(184,198,204,0) 70%);
  }
  .site-header {
    position: absolute; left: 0; top: 0; width: 1024px; height: 80px;
    background: var(--header-band);
  }
  .brand {
    position: absolute; left: 128px; top: 26px;
    font-size: 24px; font-weight: 300; color: var(--accent); letter-spacing: 0.3px;
  }
  .main-nav {
    position: absolute; right: 128px; top: 31px;
    display: flex; gap: 22px; font-size: 12.5px; font-weight: 400; color: #d6dde2;
  }
  .main-nav .is-active { color: var(--accent); }
  .hero-arrow { position: absolute; top: 250px; }
  .hero-arrow.prev { left: 124px; }
  .hero-arrow.next { left: 884px; }
  .hero-caption {
    position: absolute; left: 0; top: 380px; width: 800px; height: 68px;
    background: linear-gradient(90deg, var(--caption-band) 85%, rgba(20,24,18,0));
  }
  .hero-caption p {
    position: absolute; left: 138px; top: 10px; white-space: nowrap;
    font-family: "Dancing Script", cursive; font-size: 36px; color: var(--white);
  }
  .hero-caption em { font-style: normal; color: var(--accent); }

  /* Sections */
  .section-title {
    position: absolute; left: 0; width: 1024px; text-align: center;
    font-size: 28px; font-weight: 400; color: var(--accent); letter-spacing: 0.3px;
  }
  .rule { position: absolute; left: 128px; width: 768px; height: 1px; background: var(--rule); }

  .feature-list {
    position: absolute; left: 0; width: 1024px; text-align: center;
    font-size: 15.5px; text-transform: uppercase; line-height: 24px; color: var(--text);
  }
  .feature-list .sep { margin: 0 14px; }

  .gallery-thumb { position: absolute; top: 699px; width: 146px; height: 106px; }
  .gallery-arrow { position: absolute; top: 743px; font-size: 18px; font-weight: 400; color: #222; }

  .sale-photo { position: absolute; top: 912px; height: 176px; }
  .sale-photo.interior { left: 128px; width: 240px; border: 3px solid var(--frame); }
  .sale-photo.interior div { width: 100%; height: 100%; background: linear-gradient(180deg, #d9d4cc 0%, #9a8a76 55%, #4a2a18 100%); }
  .sale-photo.terrace { left: 376px; width: 278px; }

  .info-panel {
    position: absolute; left: 659px; top: 915px; width: 234px; height: 170px;
    background: var(--panel); padding: 10px 13px;
  }
  .info-panel h3 { font-size: 17px; font-weight: 400; color: var(--accent); margin-bottom: 16px; }
  .info-panel dl { font-size: 13.5px; line-height: 22.4px; text-transform: uppercase; color: #777; }
  .info-panel dt, .info-panel dd { display: inline; }
  .info-panel dd::after { content: ""; display: block; }

  /* Footer */
  .footer-nav { position: absolute; left: 128px; top: 1139px; font-size: 11px; font-weight: 400; color: var(--text-dark); }
  .footer-nav .is-active { color: var(--accent); }
  .footer-nav .sep { margin: 0 8px; }
  .copyright { position: absolute; left: 128px; top: 1164px; font-size: 10.5px; font-weight: 400; color: var(--text-dark); }
  .social { position: absolute; right: 128px; top: 1150px; display: flex; align-items: center; gap: 10px; font-size: 10.5px; font-weight: 400; color: var(--text-dark); }
  .social a { display: flex; align-items: center; gap: 4px; color: #7a7a7a; }
  .social a span.mark { width: 10px; height: 10px; background: #8d8d8d; display: inline-block; }
</style>
</head>
<body>

<section class="hero">
  <div role="img" aria-label="Aerial photograph of Barra Da Tijuca coastline, beach, towers, lagoon and green hills" style="position:absolute;inset:0;"></div>
  <div class="hero-lake"></div>

  <header class="site-header">
    <a class="brand" href="#">Skyline Residence</a>
    <nav class="main-nav">
      <a class="is-active" href="#">Home</a>
      <a href="#">Tranquil Cliff Suites</a>
      <a href="#">The Apartment</a>
    </nav>
  </header>

  <svg class="hero-arrow prev" width="14" height="56" viewBox="0 0 14 56" aria-label="Previous slide"><polyline points="12,2 2,28 12,54" fill="none" stroke="#fff" stroke-width="1.5"/></svg>
  <svg class="hero-arrow next" width="14" height="56" viewBox="0 0 14 56" aria-label="Next slide"><polyline points="2,2 12,28 2,54" fill="none" stroke="#fff" stroke-width="1.5"/></svg>

  <div class="hero-caption">
    <p>My penthouse which is located at <em>Barra Da Tijuca</em></p>
  </div>
</section>

<h2 class="section-title" style="top:503px;">FEATURES</h2>
<div class="feature-list" style="top:546px;">
  Maids room with bath<span class="sep">-</span>Guest bathroom<span class="sep">-</span>Living room<span class="sep">-</span>Dinning room<span class="sep">-</span><br>
  Terrace with heated pool for year round use<span class="sep">-</span>Veranda
</div>
<div class="rule" style="top:623px;"></div>

<h2 class="section-title" style="top:647px;">GALLERY</h2>
<span class="gallery-arrow" style="left:96px;">&#10216;</span>
<div class="gallery-thumb" style="left:119px;background:linear-gradient(180deg,#dfe6ea 0%,#b9bcbc 50%,#8a8e8c 100%);" role="img" aria-label="Rooftop terrace with parasols and white tables"></div>
<div class="gallery-thumb" style="left:279px;background:linear-gradient(180deg,#6a6a3c 0%,#5fb5c6 40%,#b3a57a 100%);" role="img" aria-label="Condominium pool seen from above"></div>
<div class="gallery-thumb" style="left:439px;background:linear-gradient(180deg,#a06a58 0%,#9aa6a2 40%,#5e8a3a 80%,#6c6a60 100%);" role="img" aria-label="Condominium entrance gate with garden"></div>
<div class="gallery-thumb" style="left:599px;background:linear-gradient(180deg,#cfd8dc 0%,#9aa496 45%,#e4e4e2 75%,#cfcfcf 100%);" role="img" aria-label="Penthouse terrace with barbecue and red railing"></div>
<div class="gallery-thumb" style="left:759px;background:linear-gradient(180deg,#9fb0b8 0%,#8a8a78 40%,#3e5028 75%,#6a2a24 100%);" role="img" aria-label="View of the mountains from the veranda"></div>
<span class="gallery-arrow" style="left:918px;">&#10217;</span>
<div class="rule" style="top:839px;"></div>

<h2 class="section-title" style="top:862px;">PENTHOUSE SALE</h2>
<div class="sale-photo interior"><div role="img" aria-label="Living room with wooden floor, artwork and staircase"></div></div>
<svg class="sale-photo terrace" width="278" height="176" viewBox="0 0 278 176" role="img" aria-label="Terrace with heated pool and sun loungers">
  <defs>
    <linearGradient id="terrace-tone" x1="0" y1="0" x2="0" y2="1">
      <stop offset="0" stop-color="#eeeeee"/>
      <stop offset="0.35" stop-color="#3c4650"/>
      <stop offset="0.7" stop-color="#5a6670"/>
      <stop offset="0.85" stop-color="#3fa8c8"/>
      <stop offset="1" stop-color="#7a3a24"/>
    </linearGradient>
  </defs>
  <polygon points="0,0 240,0 278,88 240,176 0,176" fill="var(--frame)"/>
  <polygon points="3,3 237,3 274,88 237,173 3,173" fill="url(#terrace-tone)"/>
</svg>

<aside class="info-panel">
  <h3>PENTHOUSE INFORMATION</h3>
  <dl>
    <dt>Size</dt> <dd>&nbsp;&nbsp;- 251 sq m</dd>
    <dt>Type</dt> <dd>&nbsp;&nbsp;- Duplex penthouse</dd>
    <dt>Style</dt> <dd>&nbsp;- 4 suites</dd>
    <dt>Price</dt> <dd>&nbsp;&nbsp;-&nbsp; R$ 2.200.000</dd>
    <dt>Price per sq m</dt> <dd>- R$ 8.764</dd>
  </dl>
</aside>
<div class="rule" style="top:1119px;"></div>

<footer>
  <nav class="footer-nav">
    <a class="is-active" href="#">Home</a><span class="sep">:</span><a href="#">Tranquil Cliff Suites</a><span class="sep">:</span><a href="#">The Apartment</a>
  </nav>
  <p class="copyright">© Copyright 2011. All rights reserved.</p>
  <div class="social">
    <span>Follow us on</span>
    <a href="#"><span class="mark"></span>Chirpline</a>
    <a href="#"><span class="mark"></span>Gatherly</a>
    <a href="#"><span class="mark"></span>Worknet</a>
  </div>
</footer>

</body>
</html>
```